Design a modern, classy & professional business card for an online real estate agency, specializing in medium-luxury properties in Thailand and later in Singapore and UK.

Possible design ideas so far: (not essential)

- curved corner(s) to the card, white on front & turquoise on back or visa versa.

- front of card - clear and simple, company name in metallic grey/monochrome, logo graphic & company name on front in spot UV or embossed/debossed effect.

- back of card - large, close-cropped, 'ghost' patterns of the C-shaped curves of logo, or company name repeated on back of card in spot UV.

Target Market(s)

- young to middle-aged professionals mainly (but ideally should design should suit all)

- UK, US,EU,AUS & ASIAN mainly (but ideally should design should suit all countries)

Industry/Entity Type

Real Estate

Requirements
Must have
• THEME:
- Luxurious & Modern
- Clean & striking
- Unique & creative

INFO:
- Logo & company name on front
- Contact details on back:

Tobias Hennlund
Managing Director

www.velmontestates.asia
www.velmontestates.co.uk

Tel: 083-274-6159
email: tobias@velmontestates.asia

(contact details can be displayed in any order as suites design.)

Nice to have
• - curved corner(s) to the card, white on front & turquoise on back or visa versa.

Should not have
• - No generic images of properties, palm trees/coconut trees etc.

- No other other bold colors, except for main turquoise, grey, metallic white & black theme.

- No obvious business card templates

```html
<!DOCTYPE html>
<html lang="en">
<head>
<meta charset="utf-8">
<title>Velmont Estates – Business Card</title>
<link rel="stylesheet" href="https://fonts.googleapis.com/css2?family=Tinos&family=Arimo&display=swap">
<style>
  :root {
    --stage-dark: #050606;
    --stage-glow: #7a8a80;
    --turquoise: #97e4df;
    --turquoise-soft: #b9ede9;
    --turquoise-deep: #1cc1b6;
    --ghost: #d3f3f1;
    --paper: #ffffff;
    --metal-grey: #6c6e70;
    --rule-grey: #8e9092;
    --ink: #1a1010;
  }
  * { margin: 0; padding: 0; box-sizing: border-box; }
  html, body { width: 1200px; height: 889px; overflow: hidden; }
  body {
    position: relative;
    background: radial-gradient(ellipse 560px 470px at 640px 470px, var(--stage-glow) 0%, #3a433e 45%, var(--stage-dark) 100%);
    font-family: "Tinos", "Times New Roman", serif;
  }
  .card {
    position: absolute;
    width: 710px;
    height: 405px;
    border-radius: 90px 0 90px 0;
    overflow: hidden;
  }
  .card--back {
    left: 426px; top: 425px;
    background: var(--paper);
  }
  .card--front {
    left: 85px; top: 38px;
    background: var(--turquoise);
    box-shadow: 6px 8px 14px rgba(0,0,0,0.45);
    z-index: 2;
  }
  .ghost-field {
    position: absolute; inset: 0;
  }
  .card--front .ghost-field {
    background: radial-gradient(ellipse 420px 300px at 420px 140px, var(--turquoise-soft) 0%, var(--turquoise) 75%);
  }
  .card--back .ghost-field {
    background: radial-gradient(ellipse 520px 340px at 520px 240px, var(--ghost) 0%, var(--paper) 80%);
  }
  .brand {
    position: absolute;
    display: flex;
    align-items: center;
  }
  .brand__square {
    background: var(--turquoise-deep);
    flex: none;
  }
  .brand__name {
    color: var(--metal-grey);
    white-space: nowrap;
    line-height: 1;
  }
  .card--front .brand { left: 145px; top: 145px; }
  .card--front .brand__square { width: 117px; height: 117px; margin-right: 16px; }
  .card--front .brand__name { font-size: 48px; }
  .card--back .brand { left: 357px; top: 25px; }
  .card--back .brand__square { width: 88px; height: 88px; margin-right: 12px; }
  .card--back .brand__name { font-size: 29px; }
  .brand-rule {
    position: absolute;
    left: 14px; top: 69px;
    width: 326px; height: 2px;
    background: var(--rule-grey);
  }
  .holder {
    position: absolute;
    left: 0; right: 0; top: 182px;
    text-align: center;
    color: var(--ink);
  }
  .holder__name { font-size: 38px; line-height: 44px; transform: translateX(-8px); }
  .holder__role { font-size: 24px; line-height: 30px; transform: translateX(-18px); }
  .contacts {
    position: absolute;
    left: 39px; top: 311px;
    width: 607px; height: 65px;
    border-top: 1px solid var(--ink);
    border-bottom: 1px solid var(--ink);
    font-family: "Arimo", Arial, sans-serif;
    font-size: 17px;
    line-height: 23px;
    color: var(--ink);
    padding-top: 9px;
  }
  .contacts__col { position: absolute; top: 9px; }
  .contacts__col--direct { left: 2px; }
  .contacts__col--web { left: 355px; }
  .contacts__label { display: inline-block; width: 52px; }
</style>
</head>
<body>
  <section class="card card--back" aria-label="Card back">
    <div class="ghost-field" role="img" aria-label="Faint pale turquoise curved background pattern"></div>
    <div class="brand-rule"></div>
    <div class="brand">
      <span class="brand__square"></span>
      <span class="brand__name">Velmont Estates</span>
    </div>
    <div class="holder">
      <p class="holder__name">Tobias Hennlund</p>
      <p class="holder__role">Managing Director</p>
    </div>
    <div class="contacts">
      <div class="contacts__col contacts__col--direct">
        <p><span class="contacts__label">Tel&nbsp;&nbsp;&nbsp;&nbsp;</span>: 083-274-6159</p>
        <p>email : tobias@velmontestates.asia</p>
      </div>
      <div class="contacts__col contacts__col--web">
        <p>www.velmontestates.asia</p>
        <p>www.velmontestates.co.uk</p>
      </div>
    </div>
  </section>

  <section class="card card--front" aria-label="Card front">
    <div class="ghost-field" role="img" aria-label="Large ghosted turquoise curved background pattern"></div>
    <div class="brand">
      <span class="brand__square"></span>
      <span class="brand__name">Velmont Estates</span>
    </div>
  </section>
</body>
</html>
```